Varelko App for Smart Devices IoT WiFi Electronic

Varelko is a siren manufacturer. This application is used for the company's products that have a Wi-Fi connection and an internet connection, which can be configured and activated remotely through this application. In addition, this application is used to activate the siren at specific times for the start and end of shifts in companies and schools. Users will be siren installers and IT or HR managers.
In addition to activating motorized sirens timers, some siren models have speakers and allow you to play TTS (text to speech) audio, audio recorded by the user on the phone and upload audio (mp3) with playlist programming with start and end times.
Application screens: home with dashboard (one dashboard for each category). Device categories: timers, speakers, motorized siren. Screen for requesting evaluation in the Play Store. Screen for registering the user profile. Screen for registering devices according to their category (timers, speakers, motorized siren). Screen for registering device groups. Screen for pairing the device on the client's Wi-Fi network. Screen for registering activation times. Screen for uploading MP3 audios. Screen for registering playlists with audio selection, start and end times. Screen for recording audio for later sending to the speakers. Screen for converting text to speech and sending to the speakers. It is important to have a time picker with the day of the week to program the activation times and playlist.

Target Market(s)

Schools, Companies and Stores.

Industry/Entity Type

IoT

Font styles to use
Sans Serif
Other font styles liked:
• roboto

Colors
FFC000
F8CF3A
FAE287
FDF2CF
FEFAEE

Requirements
Must have
• time picker with weekdays for timer programming feature.
Nice to have
• app review request screen on play store

```html
<!DOCTYPE html>
<html lang="en">
<head>
<meta charset="UTF-8">
<title>Varelko – Sign Up</title>
<link href="https://fonts.googleapis.com/css2?family=Roboto:wght@400;500;700&display=swap" rel="stylesheet">
<style>
  :root {
    --amber: #F2BE00;
    --yellow-1: #F8CF3A;
    --yellow-2: #FAE287;
    --yellow-3: #F3D792;
    --cream: #FEFAEE;
    --white: #FFFFFF;
    --ink: #111111;
    --label: #5B5B5B;
    --muted: #6F6F6F;
    --field-border: #ECECEC;
    --icon: #A3A3A3;
    --stage: #F2F2F2;
  }
  * { box-sizing: border-box; margin: 0; padding: 0; }
  html, body {
    width: 1200px; height: 2181px; overflow: hidden;
    background: var(--stage);
    font-family: "Roboto", Arial, sans-serif;
  }
  .screen {
    position: absolute; left: 97px; top: 0;
    width: 1005px; height: 2181px; overflow: hidden;
    background: linear-gradient(170deg, var(--yellow-3) 0%, var(--yellow-2) 35%, var(--yellow-1) 100%);
  }
  .status-bar {
    position: absolute; left: 56px; right: 48px; top: 26px; height: 44px;
    display: flex; align-items: center; justify-content: space-between;
  }
  .status-time { font-size: 35px; font-weight: 700; color: var(--ink); }
  .status-icons { display: flex; gap: 12px; align-items: center; }
  .brand-name {
    position: absolute; top: 430px; width: 100%; text-align: center;
    font-size: 180px; font-weight: 500; color: var(--white); letter-spacing: 2px; line-height: 1;
  }
  .page-title {
    position: absolute; top: 650px; width: 100%; text-align: center;
    font-size: 75px; font-weight: 700; color: var(--ink);
  }
  .page-subtitle {
    position: absolute; top: 776px; width: 100%; text-align: center;
    font-size: 27px; color: var(--ink);
  }
  .form-card {
    position: absolute; left: 0; top: 1005px; transform: translateY(-95px);
    width: 1005px; height: 1400px; background: var(--white);
    border-radius: 106px 106px 0 0;
  }
  .field { position: absolute; }
  .field-label { display: block; font-size: 27px; color: var(--label); margin-bottom: 16px; }
  .field-input {
    height: 106px; border: 2px solid var(--field-border); border-radius: 21px;
    display: flex; align-items: center; justify-content: space-between;
    padding: 0 32px; font-size: 32px; color: var(--ink);
  }
  .field-input.secret { letter-spacing: 4px; font-size: 30px; }
  .btn-register {
    position: absolute; left: 51px; top: 971px; width: 902px; height: 112px;
    background: var(--amber); border-radius: 21px; color: var(--white);
    font-size: 32px; display: flex; align-items: center; justify-content: center;
  }
  .login-prompt {
    position: absolute; top: 1142px; width: 100%; text-align: center;
    font-size: 27px; color: var(--muted);
  }
  .login-link { color: var(--amber); font-weight: 500; margin-left: 14px; }
</style>
</head>
<body>
<main class="screen">
  <div class="status-bar">
    <span class="status-time">09:41</span>
    <span class="status-icons">
      <svg width="40" height="26" viewBox="0 0 40 26"><rect x="0" y="18" width="7" height="8" rx="1.5" fill="#111"/><rect x="10" y="13" width="7" height="13" rx="1.5" fill="#111"/><rect x="20" y="7" width="7" height="19" rx="1.5" fill="#111"/><rect x="30" y="1" width="7" height="25" rx="1.5" fill="#111" opacity=".35"/></svg>
      <svg width="36" height="26" viewBox="0 0 36 26"><path d="M18 25 L12 18 A9 9 0 0 1 24 18 Z" fill="#111"/><path d="M6 12 A17 17 0 0 1 30 12" stroke="#111" stroke-width="4" fill="none"/><path d="M1 6 A24 24 0 0 1 35 6" stroke="#111" stroke-width="4" fill="none"/></svg>
      <svg width="52" height="26" viewBox="0 0 52 26"><rect x="1" y="2" width="44" height="22" rx="6" fill="none" stroke="#111" stroke-width="2" opacity=".4"/><rect x="4" y="5" width="38" height="16" rx="4" fill="#111"/><rect x="47" y="9" width="4" height="8" rx="2" fill="#111" opacity=".4"/></svg>
    </span>
  </div>

  <div class="brand-name">Varelko</div>
  <h1 class="page-title">Sign Up</h1>
  <p class="page-subtitle">Create an account to continue!</p>

  <section class="form-card">
    <div class="field" style="left:56px; top:162px; width:428px;">
      <span class="field-label">First Name</span>
      <div class="field-input">Lois</div>
    </div>
    <div class="field" style="left:521px; top:162px; width:431px;">
      <span class="field-label">Last Name</span>
      <div class="field-input">Jhone</div>
    </div>
    <div class="field" style="left:56px; top:361px; width:898px;">
      <span class="field-label">Email</span>
      <div class="field-input">Abc@vrk.com</div>
    </div>
    <div class="field" style="left:56px; top:561px; width:898px;">
      <span class="field-label">Password</span>
      <div class="field-input secret">*******
        <svg width="34" height="30" viewBox="0 0 34 30"><path d="M2 15 C8 5 26 5 32 15 C26 25 8 25 2 15 Z" fill="none" stroke="var(--icon)" stroke-width="2.5"/><circle cx="17" cy="15" r="5" fill="none" stroke="var(--icon)" stroke-width="2.5"/><line x1="5" y1="27" x2="29" y2="3" stroke="var(--icon)" stroke-width="2.5"/></svg>
      </div>
    </div>
    <div class="field" style="left:56px; top:763px; width:898px;">
      <span class="field-label">Confirm Password</span>
      <div class="field-input secret">*******
        <svg width="34" height="30" viewBox="0 0 34 30"><path d="M2 15 C8 5 26 5 32 15 C26 25 8 25 2 15 Z" fill="none" stroke="var(--icon)" stroke-width="2.5"/><circle cx="17" cy="15" r="5" fill="none" stroke="var(--icon)" stroke-width="2.5"/><line x1="5" y1="27" x2="29" y2="3" stroke="var(--icon)" stroke-width="2.5"/></svg>
      </div>
    </div>

    <div class="btn-register">Registor</div>
    <p class="login-prompt">Already have an account?<span class="login-link">Login</span></p>
  </section>
</main>
</body>
</html>
```